July 2022 Industrial Manufacturer Product Expo Mexico City

We manufacture large screws and fastners for large Mining equipment, Trains, large ships, airplanes, wind turbines, and so on. We also do custom work base on the customer needs. No matter the size we can make it.
We have a Expo coming up with companies all over the world. We have to stand out we are a family own business so our customer service will be above and beyond anyone can provide. We do not have a sales force to push our products and services we provide one on one service.
Plus@!! I'm looking for anything that you designers can come up with if it was your company to put on a business card, plus i want to do a 1 or 2 sided pamphlet, and then a website. We make Speciality Bolts for large mining equipment these bolts can be 3 to 4 foot long!!! Plus fasteners, Nuts, washers, any, size, strengths, special materials, we offer more of a ono on one customer service, We are a small company, family own, but can fulfill any type of orders. We can also provide special time lines for emergency orders. "We keep the machines running we here at KRV don't believe in down time" We want to hear any slogan based on our company to stand out.
Thanks i really appreciate all your work and options that we have to pick on. Plus just a thought we could possibly want to entertain a experience Marketing internet help maybe a employment possibility. Thanks

I need 2 cards one in Spanish and English Like the steel back ground maybe send me in some bright red and blue writing Same with the Black cards Please remove the word Military The logo KRV maybe integrate a picture of a Bolt 🔩 Thank you

Still looking for I need 2 cards one in Spanish and English Like the steel back ground maybe send me in some bright red and blue writing Same with the Black cards try bright writing Please remove the word Military The logo KRV maybe integrate a picture of a Bolt 🔩 Plus will need the company to make a brochure and website next Thank you

Target Market(s)

Large Mining, Ship, Train, Green Energy, VELM, and Government equipment. Throughout the World

Industry/Entity Type

We can Custom Manufacture any type of Fastners for Mining equipment, Trains, Ships, Green energy, Governments, or military projects. wind turbines,

Contact Information for Business Card

I attached the name and contact info that's on a card, plus the Company Logo. Would like industrial looking background with Bright Colors that will stand out!! If we can insert somewhere maybe on back that we "Custom Manufacture Any Size or Quantity Fastners for Large Mining Equipment, Trains, Ships, Green Energy Equipment or Government Projects

Font styles to use
Other font styles liked:
• You Pick, has to be bold, colorful standout, Professional looking Beable to read it.

Colors

Designer to choose colors to be used in the design.

Requirements
Must have
• Need in Spanish and English TO STANDOUT FROM THE REST OF THE EXPO!! See Business card details, Rounded corners
Nice to have
• Can i see some of the darker cards with Bright Red and Blue letters I like to see the different type of card material, heavy thickness, plastic, transparent, Metal types, Bright Colors, I saw like Raised letters like on the logo.

```html
<!DOCTYPE html>
<html lang="es">
<head>
<meta charset="utf-8">
<title>KRV – Business Card</title>
<link href="https://fonts.googleapis.com/css2?family=Bebas+Neue&family=Source+Sans+3:wght@400;600;700&display=swap" rel="stylesheet">
<style>
  :root {
    --backdrop: #dcdcdc;
    --card-blue-light: #009ad9;
    --card-blue-deep: #0a1f7f;
    --card-white: #ffffff;
    --ink-white: #ffffff;
    --ink-navy: #1b2b5e;
    --ink-accent: #0b93d0;
    --ink-mark: #3a3a3e;
    --shadow: rgba(0, 0, 0, 0.35);
  }
  * { margin: 0; padding: 0; box-sizing: border-box; }
  html, body {
    width: 1200px;
    height: 900px;
    overflow: hidden;
    background: var(--backdrop);
  }
  .stage {
    position: relative;
    width: 1200px;
    height: 900px;
  }
  .card {
    position: absolute;
    top: 217px;
    width: 309px;
    height: 500px;
    box-shadow: 2px 3px 5px var(--shadow);
  }
  .card--back {
    left: 279px;
    border-radius: 0 62px 0 62px;
    background: linear-gradient(225deg, var(--card-blue-light) 0%, #0466b4 40%, var(--card-blue-deep) 100%);
    color: var(--ink-white);
  }
  .card--front {
    left: 617px;
    border-radius: 62px 0 62px 0;
    background: var(--card-white);
  }
  .brand-name {
    position: absolute;
    left: 0;
    width: 100%;
    text-align: center;
    font-family: "Source Sans 3", sans-serif;
    font-weight: 700;
    font-size: 66px;
    letter-spacing: 6px;
    line-height: 1;
  }
  .card--back .brand-name {
    top: 140px;
    color: var(--ink-white);
  }
  .card--front .brand-name {
    top: 130px;
    color: var(--ink-mark);
  }
  .capabilities {
    position: absolute;
    top: 310px;
    left: 0;
    width: 100%;
    text-align: center;
    font-family: "Bebas Neue", sans-serif;
    font-size: 24px;
    line-height: 27.8px;
    letter-spacing: -0.2px;
  }
  .contact {
    position: absolute;
    left: 28px;
    top: 325px;
    font-family: "Source Sans 3", sans-serif;
    color: var(--ink-navy);
  }
  .contact__name {
    font-size: 18.5px;
    font-weight: 600;
    color: var(--ink-accent);
    margin-bottom: 20px;
    white-space: nowrap;
  }
  .contact__quote {
    font-size: 14px;
    line-height: 19px;
    margin-bottom: 14px;
  }
  .contact__phone {
    display: flex;
    align-items: center;
    gap: 6px;
    font-size: 14px;
    line-height: 18px;
  }
  .contact__phone svg { width: 13px; height: 13px; flex: none; }
</style>
</head>
<body>
  <main class="stage">
    <section class="card card--back" aria-label="Card back">
      <div class="brand-name">KRV</div>
      <p class="capabilities">
        Custom manufacture any size<br>
        or&nbsp; quantity fasteners for large<br>
        mining equipment trains, ships<br>
        green energy&nbsp; equipment<br>
        or government&nbsp; projects
      </p>
    </section>

    <section class="card card--front" aria-label="Card front">
      <div class="brand-name">KRV</div>
      <div class="contact">
        <p class="contact__name">Lic. Marisol Vega Treviño</p>
        <p class="contact__quote">Cotizaciones en<br>krv.ventas@correo-ejemplo.mx</p>
        <p class="contact__phone">
          <svg viewBox="0 0 16 16" aria-hidden="true"><path d="M4 1.5 6 4.5 4.8 6c.8 1.9 2.3 3.4 4.2 4.2L10.5 9l3 2-1.3 2.6C7 13.6 2.4 9 2.4 3.8Z" fill="none" stroke="#0b93d0" stroke-width="1.5" stroke-linejoin="round"/><path d="M9.5 2.5a4 4 0 0 1 4 4M9.5 5a1.6 1.6 0 0 1 1.6 1.6" fill="none" stroke="#0b93d0" stroke-width="1.3" stroke-linecap="round"/></svg>
          5550148820
        </p>
        <p class="contact__phone">
          <svg viewBox="0 0 16 16" aria-hidden="true"><rect x="4" y="1.5" width="8" height="13" rx="1.5" fill="none" stroke="#0b93d0" stroke-width="1.5"/><circle cx="8" cy="12" r="0.9" fill="#0b93d0"/></svg>
          5550193471
        </p>
      </div>
    </section>
  </main>
</body>
</html>
```